Flyer für Photovoltaik- und Energiesysteme
Zielgruppe
Die Merkling Strom GmbH entwickelt und realisiert seit über 20 Jahren Photovoltaik- und Energiesysteme für Unternehmen, Kommunen und öffentliche Einrichtungen.
Ziel dieses Flyers sind Bürgermeister, Oberbürgermeister, Kämmerer, Bauämter und kommunale Entscheidungsträger sowie Gemeinderatsmitglieder und Mitarbeiter der Gemeinden und Städte.
Der Flyer soll zeigen, dass Kommunen auch bei knappen Haushalten wirtschaftlich von Photovoltaik profitieren können. Dabei sollen insbesondere Bürgersolaranlagen, Fremdfinanzierung, Eigenverbrauchskonzepte und Energy Sharing verständlich und positiv dargestellt werden.
Der Flyer soll Vertrauen schaffen, Kompetenz vermitteln und zu einem persönlichen Gespräch motivieren.
Aufgabenstellung
Modernes, hochwertiges und professionelles Design. Wahrscheinlich DIN A4 Hochformat, offen für Vorschläge.
Zielgruppe sind Kommunen und öffentliche Entscheidungsträger, daher bitte keine „Werbeflyer Optik“, sondern seriös, vertrauenswürdig und wirtschaftlich.
Farben und Corporate Design an Merkling Strom anlehnen (Grün- und Weißtöne).
Merkling Strom Logo verwenden.
Bildsprache:
• moderne Rathäuser und Kommunalgebäude
• Photovoltaikanlagen auf öffentlichen Gebäuden
• Bürgerbeteiligung und regionale Wertschöpfung
• nachhaltige und wirtschaftliche Energieversorgung
Die Kernaussage lautet:
„Kommunen – Chancen nutzen, auch in Zeiten knapper Budgets.“
Folgende Lösungswege könnten grafisch dargestellt werden:
A) Eigenerzeugung Kommunale PV Anlagen auf eigenen Gebäuden (Eigeninvestion)
B) Ohne eigene Investition durch
-Stromverkaufsmodelle (onside PPA)
-Bürgersolaranlagen und Fremdfinanzierung
C) Energy Sharing (seit Juni 2026 möglich)
Lokale Nutzung und Verteilung erneuerbarer Energie.
Der Flyer soll vermitteln, dass die Energiewende nicht an fehlenden Haushaltsmitteln scheitern muss. Ich habe erste Entwurfe bereits von ChatGPT machen lassen, Text, Layout und Inhalt gefallen mir aber selbst eigentlich nicht und dienen eher ein wenig zur Inspiration und Verständnis.
Wichtig: Wenig Text, starke Grafiken, moderne Icons und eine hochwertige Gestaltung. Der Flyer soll eher wie eine Management Broschüre als wie ein klassischer Werbeflyer wirken.

```html
<!DOCTYPE html>
<html lang="de">
<head>
<meta charset="utf-8">
<title>Merkling Strom – Flyer Kommunen</title>
<link rel="stylesheet" href="https://fonts.googleapis.com/css2?family=Barlow+Semi+Condensed:wght@700&family=Lexend:wght@300;400;500&display=swap">
<style>
  :root {
    --green-dark: #0b5a45;
    --green-mid: #2f7a3c;
    --green-lime: #6f9c3a;
    --green-soft: #c7dcb3;
    --white: #ffffff;
    --ink: #1f2a24;
    --stage: #e8eee6;
  }
  * { box-sizing: border-box; margin: 0; padding: 0; }
  html, body { width: 1200px; height: 629px; overflow: hidden; background: var(--stage); }
  body { display: flex; align-items: center; justify-content: center; font-family: "Lexend", sans-serif; color: var(--ink); }

  .flyer { position: relative; width: 427px; height: 600px; background: var(--white); box-shadow: 0 2px 12px rgba(0,0,0,.12); overflow: hidden; }

  .hero { position: absolute; left: 0; top: 0; width: 427px; height: 160px;
    background: linear-gradient(180deg, #b9d3e6 0%, #d7e4d8 40%, #6e8f55 62%, #4b7a30 100%); }
  .hero-shade { position: absolute; inset: 0; background: linear-gradient(90deg, rgba(20,60,20,.55) 0%, rgba(20,60,20,.1) 70%); }
  .brand { position: absolute; left: 14px; top: 22px; display: flex; align-items: center; gap: 6px;
    font-weight: 500; font-size: 19px; color: var(--green-dark); }
  .brand-dot { width: 14px; height: 14px; border-radius: 50%; background: var(--green-dark); }
  .seal { position: absolute; right: 20px; top: 18px; width: 50px; height: 50px; border-radius: 50%;
    background: var(--green-lime); border: 3px solid var(--white); }
  .hero-title { position: absolute; left: 16px; top: 92px; color: var(--white); font-size: 16px; line-height: 1.4; font-weight: 400; }
  .hero-title strong { font-weight: 500; }

  .tagline { position: absolute; right: 13px; top: 160px; padding-top: 5px; text-align: right;
    font-size: 9.4px; line-height: 1.4; color: var(--green-dark); font-weight: 400; }

  .section { position: absolute; left: 0; width: 427px; }
  .section-text-right { background: linear-gradient(90deg, var(--green-lime) 0%, var(--green-soft) 40%, var(--white) 75%); }
  .section-text-left { background: linear-gradient(90deg, var(--white) 0%, var(--white) 40%, var(--green-soft) 75%, var(--green-lime) 100%); }
  .photo { position: absolute; top: 0; bottom: 0; }
  .section-title { font-family: "Barlow Semi Condensed", sans-serif; font-weight: 700; color: var(--green-dark);
    font-size: 18px; line-height: 1.22; letter-spacing: .2px; }
  .bullets { list-style: none; font-size: 9.8px; line-height: 1.34; font-weight: 300; color: var(--ink); }
  .bullets li::before { content: "• "; }

  .s-own { top: 191px; height: 83px; }
  .s-own .copy { position: absolute; left: 13px; top: 3px; }
  .s-own .bullets { margin-top: 4px; }
  .s-own .photo { left: 281px; right: 0; background: linear-gradient(180deg, #bcd4ea 0%, #3a4f86 45%, #5d8a3a 100%); }

  .band { position: absolute; left: 0; width: 427px; height: 11px; background: var(--green-dark); }
  .band-1 { top: 274px; }
  .band-2 { top: 413px; }

  .s-sale { top: 285px; height: 128px; }
  .s-sale .photo { left: 0; width: 171px; background: linear-gradient(180deg, #8ea6c8 0%, #9db1c6 45%, #6f8b5c 100%); }
  .s-sale .copy { position: absolute; right: 13px; top: 4px; text-align: right; }
  .s-sale .copy-body { position: absolute; left: 222px; top: 48px; }
  .s-sale .lead { font-size: 9.8px; line-height: 1.34; font-weight: 300; color: var(--green-lime); }
  .s-sale .bullets { margin-top: 3px; }

  .s-share { top: 424px; height: 84px; }
  .s-share .copy { position: absolute; left: 13px; top: 3px; }
  .s-share .bullets { margin-top: 3px; }
  .s-share .photo { left: 281px; right: 0; background: linear-gradient(160deg, #4d7a3a 0%, #3c5a4a 50%, #5e8a40 100%); }

  .keywords { position: absolute; left: 0; top: 508px; width: 427px; height: 18px; background: var(--green-dark);
    color: var(--white); font-size: 5.6px; line-height: 18px; padding-left: 13px; white-space: nowrap; }

  .footer { position: absolute; left: 0; top: 526px; width: 427px; height: 74px; padding: 7px 13px 0; }
  .cta { font-size: 9.6px; line-height: 1.4; font-weight: 300; color: var(--green-dark); }
  .cta-sub { font-size: 9.6px; line-height: 1.4; font-weight: 300; color: var(--green-lime); }
  .contact { position: absolute; top: 38px; font-size: 9.4px; line-height: 1.5; font-weight: 300; color: var(--ink); white-space: nowrap; }
  .contact-a { left: 15px; }
  .contact-b { left: 160px; }
  .contact p { display: flex; align-items: center; gap: 5px; }
  .contact svg { width: 10px; height: 10px; flex: none; }
  .brand-small { position: absolute; right: 14px; top: 40px; display: flex; align-items: center; gap: 4px;
    font-size: 8.5px; font-weight: 500; color: var(--green-dark); }
  .brand-small .brand-dot { width: 8px; height: 8px; }
</style>
</head>
<body>
  <article class="flyer">
    <header class="hero" role="img" aria-label="Foto: Carport mit Solarmodulen auf grüner Wiese, Kiefern und Windräder im Hintergrund">
      <div class="hero-shade"></div>
      <div class="brand"><span class="brand-dot"></span>Merkling Strom</div>
      <div class="seal"></div>
      <h1 class="hero-title"><strong>Kommunen:</strong><br>Chancen nutzen.<br>Auch in Zeiten knapper Budgets.</h1>
    </header>

    <p class="tagline">Drei Wege für Ihre Kommune<br>– heute handeln, morgen profitieren.</p>

    <section class="section s-own section-text-left">
      <div class="copy">
        <h2 class="section-title">EIGENERZEUGUNG</h2>
        <ul class="bullets">
          <li>PV auf kommunalen Dach- und Freiflächen</li>
          <li>Eigenverbrauch für Liegenschaften</li>
          <li>Unabhängigkeit von Energiepreisen</li>
          <li>Beitrag zum Klimaschutz</li>
        </ul>
      </div>
      <div class="photo" role="img" aria-label="Foto: Freiflächen-Solaranlage unter blauem Himmel"></div>
    </section>

    <div class="band band-1"></div>

    <section class="section s-sale section-text-right">
      <div class="photo" role="img" aria-label="Foto: zwei Geschäftspartner reichen sich vor Solarmodulen die Hand"></div>
      <div class="copy">
        <h2 class="section-title">STROMVERKAUF<br>OHNE INVESTITION</h2>
      </div>
      <div class="copy-body">
        <p class="lead">Mit Hilfe von Bürgersolaranlagen<br>und Fremdfinanzierung.</p>
        <ul class="bullets">
          <li>Keine eigene Investition</li>
          <li>Bürgerbeteiligung stärkt Akzeptanz</li>
          <li>Einnahmen durch Stromverkauf</li>
          <li>Partner übernimmt Planung &amp; Betrieb</li>
        </ul>
      </div>
    </section>

    <div class="band band-2"></div>

    <section class="section s-share section-text-left">
      <div class="copy">
        <h2 class="section-title">ENERGY SHARING</h2>
        <ul class="bullets">
          <li>Strom lokal teilen und nutzen</li>
          <li>Stärkung der Gemeinschaft</li>
          <li>Mehrwert für Bürger &amp; Unternehmen</li>
          <li>Schritt zur Energiewende vor Ort</li>
        </ul>
      </div>
      <div class="photo" role="img" aria-label="Luftbild: Solarpark neben Gewerbegebiet und Wald"></div>
    </section>

    <div class="keywords">• Haushaltsentlastung • Unabhängigkeit &amp; Versorgungssicherheit • Nachhaltigkeit &amp; Klimaschutz • Bürgerbeteiligung &amp; Akzeptanz •</div>

    <footer class="footer">
      <p class="cta">Jetzt die Weichen für eine starke, unabhängige und nachhaltige Kommune stellen!</p>
      <p class="cta-sub">Wir unterstützen Sie – sprechen Sie uns an.</p>
      <div class="contact contact-a">
        <p><svg viewBox="0 0 24 24" fill="none" stroke="#0b5a45" stroke-width="2"><path d="M5 3h4l2 5-3 2a11 11 0 0 0 6 6l2-3 5 2v4a2 2 0 0 1-2 2A17 17 0 0 1 3 5a2 2 0 0 1 2-2z"/></svg>+49 89 570 218 43</p>
        <p><svg viewBox="0 0 24 24" fill="none" stroke="#0b5a45" stroke-width="2"><rect x="3" y="5" width="18" height="14"/><path d="M3 5l9 8 9-8"/></svg>info@merkling-strom.de</p>
      </div>
      <div class="contact contact-b">
        <p><svg viewBox="0 0 24 24" fill="none" stroke="#0b5a45" stroke-width="2"><circle cx="12" cy="12" r="9"/><path d="M3 12h18M12 3c3 3 3 15 0 18M12 3c-3 3-3 15 0 18"/></svg>www.merkling-strom.de</p>
        <p><svg viewBox="0 0 24 24" fill="none" stroke="#0b5a45" stroke-width="2"><path d="M12 22s7-7 7-12a7 7 0 0 0-14 0c0 5 7 12 7 12z"/><circle cx="12" cy="10" r="2.5"/></svg>Lindenweg 17, 80339 München</p>
      </div>
      <div class="brand-small"><span class="brand-dot"></span>Merkling Strom</div>
    </footer>
  </article>
</body>
</html>
```